NimbaVault Website Homepage Design

Please provide your idea of homepage for a hosting company. This project is for DESIGN only, no coding.

It must use/combine colors used in logo, clean, modern look.

Homepage must consist of at least 4 sections (example: testimonials, services, and so on. not necesarily all of them). We would like the navigation to be horizontal, but not mandatory.

You can include a preview of services page (optional, not a must).

Number of Pages Required

1 page

Font styles to use
Sans Serif

```html
<!DOCTYPE html>
<html lang="en">
<head>
<meta charset="utf-8">
<title>NimbaVault – Hosting</title>
<link href="https://fonts.googleapis.com/css2?family=Montserrat:wght@300;400;500;600;700;800&family=Roboto:wght@400;500&display=swap" rel="stylesheet">
<style>
:root{
  --blue:#1474d4;
  --blue-dark:#0d5fb3;
  --navy:#0b2a4e;
  --ink:#222831;
  --text:#3d434b;
  --grey:#6f7377;
  --pale:#e4eef9;
  --mist:#eef0f4;
  --black:#030303;
  --star:#f2b33d;
  --white:#ffffff;
}
*{box-sizing:border-box;margin:0;padding:0}
html,body{width:1200px;height:3644px;overflow:hidden}
body{position:relative;background:var(--white);font-family:"Roboto",Arial,sans-serif;color:var(--text)}
.abs{position:absolute}
.head{font-family:"Montserrat",Arial,sans-serif}
.btn{position:absolute;display:flex;align-items:center;justify-content:center;background:var(--blue);color:var(--white);border-radius:24px;font-family:"Montserrat",Arial,sans-serif;font-weight:700;font-size:14px;letter-spacing:.3px;box-shadow:0 4px 10px rgba(20,116,212,.3)}
/* header */
.site-header{position:absolute;left:0;top:0;width:1200px;height:80px;border-bottom:3px solid var(--blue);background:var(--white)}
.brand{position:absolute;display:flex;align-items:center;gap:8px;font-family:"Montserrat",Arial,sans-serif;font-weight:700;color:var(--blue)}
.brand .dot{width:20px;height:20px;border-radius:50%;background:var(--blue)}
.nav{position:absolute;left:450px;top:31px;display:flex;gap:22px;font-family:"Montserrat",Arial,sans-serif;font-weight:700;font-size:12px;color:var(--ink)}
/* hero */
.hero-text{position:absolute;left:0;width:1200px;text-align:center;color:var(--white)}
.arrow{position:absolute;top:330px}
/* section titles */
.title{position:absolute;font-family:"Montserrat",Arial,sans-serif;font-size:35px;color:var(--blue);font-weight:400;letter-spacing:.3px}
.title b{font-weight:800}
.rule{position:absolute;height:4px;width:54px;background:#7d7f83}
.about-copy{position:absolute;left:575px;top:878px;width:490px;font-size:14px;line-height:30px;color:var(--text)}
/* services */
.services{position:absolute;left:0;top:1288px;width:1200px;height:703px;background:var(--pale)}
.hex{position:absolute;width:208px;height:240px}
.hex svg{position:absolute;left:0;top:0;display:block}
.hex-name{position:absolute;left:0;width:208px;text-align:center;font-family:"Montserrat",Arial,sans-serif;font-weight:600;font-size:17px;line-height:23px;color:var(--ink)}
.hex-link{position:absolute;left:0;top:182px;width:208px;text-align:center;font-family:"Montserrat",Arial,sans-serif;font-weight:600;font-size:14px;color:var(--blue)}
.hex.active .hex-name,.hex.active .hex-link{color:var(--white)}
/* testimonials */
.card{position:absolute;top:2162px;width:243px;height:244px;background:var(--white);box-shadow:0 2px 10px rgba(0,0,0,.14);padding:16px 15px}
.card.faded{opacity:.35}
.avatar{width:52px;height:52px;border-radius:50%;background:linear-gradient(135deg,#9aa7b5,#5b6b7c);float:left;margin-right:10px}
.card h4{font-family:"Montserrat",Arial,sans-serif;font-size:18px;color:var(--blue);font-weight:600;line-height:52px}
.card p{clear:both;padding-top:12px;font-size:13px;line-height:30px;color:var(--text)}
.stars{color:var(--star);font-size:13px;letter-spacing:2px;margin-top:4px}
.dots{position:absolute;left:571px;top:2453px;display:flex;gap:4px}
.dots span{width:11px;height:11px;border-radius:50%;background:#8a8d92}
.dots span.on{background:var(--blue)}
/* contact */
.contact{position:absolute;left:0;top:2547px;width:1200px;height:750px;background:var(--mist)}
.field{position:absolute;left:110px;width:395px;height:48px;border:1.5px solid #55595e;border-radius:6px;padding:14px;font-family:"Montserrat",Arial,sans-serif;font-size:13px;color:#4a4e53;background:transparent}
/* footer */
.foot-h{position:absolute;top:3346px;font-family:"Montserrat",Arial,sans-serif;font-weight:700;font-size:16px;color:var(--white)}
.foot-h::after{content:"";position:absolute;left:0;top:28px;width:64px;height:2px;background:var(--white)}
.foot-list{position:absolute;top:3392px;list-style:none;font-size:14px;line-height:30px;color:var(--white)}
.foot-list li::before{content:"»";margin-right:10px}
.foot-text{font-size:13px;line-height:24px;color:var(--white)}
.social{position:absolute;top:3584px;left:102px;display:flex;gap:12px}
.social span{width:14px;height:14px;border-radius:50%;background:var(--white)}
</style>
</head>
<body>

<header class="site-header">
  <div class="brand" style="left:110px;top:20px;font-size:32px"><span class="dot"></span>NimbaVault</div>
  <nav class="nav"><span>HOME</span><span>ABOUT US</span><span>SERVICES</span><span>TESTIMONIALS</span><span>CONTACT US</span></nav>
  <div class="btn" style="left:896px;top:15px;width:191px;height:46px">GET IN TOUCH</div>
</header>

<svg class="abs" style="left:0;top:83px" width="1200" height="625" role="img" aria-label="Photo of a glowing data center server corridor">
  <defs>
    <radialGradient id="heroGlow" cx="50%" cy="35%" r="70%">
      <stop offset="0" stop-color="#2f7fb4"/>
      <stop offset=".45" stop-color="#123f6d"/>
      <stop offset="1" stop-color="#06182f"/>
    </radialGradient>
  </defs>
  <polygon points="0,0 1200,0 1200,540 600,620 0,540" fill="url(#heroGlow)"/>
  <polyline points="0,542 600,621 1200,542" fill="none" stroke="var(--blue)" stroke-width="5"/>
</svg>
<div class="hero-text head" style="top:266px;font-size:42px;font-weight:700">LOREM IPSUM DOLOR SIT AMET CONS</div>
<div class="hero-text head" style="top:320px;font-size:42px;font-weight:400">ECTETUR ADIPISCING ELITSED DO</div>
<div class="hero-text" style="top:383px;font-size:17px">Lorem ipsum dolor sit amet, consectetur adipiscing elit, sed do eiusmod tempor</div>
<div class="btn" style="left:505px;top:425px;width:190px;height:46px">GET STARTED</div>
<svg class="arrow" style="left:54px" width="20" height="34"><polyline points="16,2 3,17 16,32" fill="none" stroke="#fff" stroke-width="3"/></svg>
<svg class="arrow" style="left:1126px" width="20" height="34"><polyline points="4,2 17,17 4,32" fill="none" stroke="#fff" stroke-width="3"/></svg>

<!-- about -->
<svg class="abs" style="left:132px;top:790px" width="350" height="414" role="img" aria-label="Photo of two engineers reviewing a laptop in a server room">
  <defs><linearGradient id="aboutFill" x1="0" y1="0" x2="1" y2="1"><stop offset="0" stop-color="#5d7898"/><stop offset="1" stop-color="#1e2f45"/></linearGradient></defs>
  <polygon points="175,4 345,104 345,310 175,410 5,310 5,104" fill="url(#aboutFill)" stroke="var(--blue)" stroke-width="5"/>
</svg>
<div class="title" style="left:575px;top:806px"><b>ABOUT</b> NIMBAVAULT</div>
<div class="rule" style="left:575px;top:856px"></div>
<p class="about-copy">Lorem ipsum dolor sit amet, consectetur adipiscing elit, sed do eiusmod tempor incididunt ut labore et dolore magna aliqua. Quis ipsum sus­pendisse ultrices gravida. Risus commodo viverra maecenas accumsan lacus vel facilisis.Sed ut perspiciatis unde omnis iste natus error sit vo­luptatem accusantium doloremque laudantium, totam rem aperiam, eaque ipsa quae ab illo inventore veritatis et quasi architecto beatae vitae dicta sunt explicabo. Nemo enim ipsam voluptatem quia voluptas sit aspernatur aut odit aut fugit, sed quia consequuntur magni.</p>
<div class="btn" style="left:575px;top:1129px;width:191px;height:47px">LEARN MORE</div>

<!-- services -->
<section class="services">
  <div class="title" style="left:0;width:1200px;text-align:center;top:78px"><b>OUR</b> SERVICES</div>
  <div class="rule" style="left:573px;top:128px"></div>
</section>

<svg width="0" height="0" class="abs"><defs>
  <polygon id="hexShape" points="104,0 208,60 208,180 104,240 0,180 0,60"/>
  <g id="icoServer" fill="none" stroke="#fff" stroke-width="2.5"><rect x="-28" y="-28" width="56" height="16" rx="2"/><rect x="-28" y="-8" width="56" height="16" rx="2"/><rect x="-28" y="12" width="56" height="16" rx="2"/><line x1="-20" y1="-20" x2="0" y2="-20"/><line x1="-20" y1="0" x2="0" y2="0"/><line x1="-20" y1="20" x2="0" y2="20"/></g>
  <g id="icoGlobe" fill="none" stroke="#1474d4" stroke-width="2.5"><circle r="28"/><ellipse rx="12" ry="28"/><line x1="-28" y1="0" x2="28" y2="0"/><line x1="-24" y1="-14" x2="24" y2="-14"/><line x1="-24" y1="14" x2="24" y2="14"/></g>
  <g id="icoCloud" fill="none" stroke="#1474d4" stroke-width="2.5"><path d="M-24,6 a12,12 0 0 1 6,-22 a16,16 0 0 1 30,2 a11,11 0 0 1 10,20 z"/><line x1="-14" y1="6" x2="-14" y2="24"/><line x1="0" y1="6" x2="0" y2="24"/><line x1="14" y1="6" x2="14" y2="24"/><line x1="-14" y1="24" x2="14" y2="24"/></g>
  <g id="icoRack" fill="none" stroke="#1474d4" stroke-width="2.5"><rect x="-30" y="-26" width="16" height="52"/><rect x="-8" y="-26" width="16" height="52"/><rect x="14" y="-26" width="16" height="52"/><line x1="-32" y1="-14" x2="32" y2="-14"/></g>
</defs></svg>

<div class="hex" style="left:113px;top:1451px"><svg width="208" height="240"><use href="#hexShape" fill="#fff"/><use href="#icoGlobe" x="104" y="78"/></svg><div class="hex-name" style="top:130px">WEB<br>HOSTING</div><div class="hex-link">Learn More</div></div>
<div class="hex active" style="left:367px;top:1451px"><svg width="208" height="240"><use href="#hexShape" fill="#1474d4"/><use href="#icoServer" x="104" y="76"/></svg><div class="hex-name" style="top:124px">WORDPRESS<br>HOSTING</div><div class="hex-link">Learn More</div></div>
<div class="hex" style="left:622px;top:1451px"><svg width="208" height="240"><use href="#hexShape" fill="#fff"/><use href="#icoRack" x="104" y="78"/></svg><div class="hex-name" style="top:124px">ECOMMERCE<br>HOSTING</div><div class="hex-link">Learn More</div></div>
<div class="hex" style="left:877px;top:1451px"><svg width="208" height="240"><use href="#hexShape" fill="#fff"/><use href="#icoGlobe" x="104" y="78"/></svg><div class="hex-name" style="top:124px">VPS</div><div class="hex-link">Learn More</div></div>
<div class="hex" style="left:240px;top:1666px"><svg width="208" height="240"><use href="#hexShape" fill="#fff"/><use href="#icoCloud" x="104" y="78"/></svg><div class="hex-name" style="top:124px">SHARED<br>HOSTING</div><div class="hex-link">Learn More</div></div>
<div class="hex" style="left:495px;top:1666px"><svg width="208" height="240"><use href="#hexShape" fill="#fff"/><use href="#icoCloud" x="104" y="78"/></svg><div class="hex-name" style="top:124px">CLOUD<br>HOSTING</div><div class="hex-link">Learn More</div></div>
<div class="hex" style="left:749px;top:1666px"><svg width="208" height="240"><use href="#hexShape" fill="#fff"/><use href="#icoGlobe" x="104" y="78"/></svg><div class="hex-name" style="top:124px">DEDICATED<br>SERVERS</div><div class="hex-link">Learn More</div></div>

<!-- testimonials -->
<div class="title" style="left:0;width:1200px;text-align:center;top:2068px"><b>OUR CLIENT</b> TESTIMONIALS</div>
<div class="rule" style="left:573px;top:2118px"></div>

<div class="card faded" style="left:-45px"><div class="avatar" role="img" aria-label="Client portrait"></div><h4>John Deo</h4><p>Lorem ipsum dolor sit amet, conse ctetur adipiscing elit, sed do eius mod tempor incididunt ut labore et dolore magna aliqua.</p><div class="stars">★★★★★</div></div>
<div class="card" style="left:216px"><div class="avatar" role="img" aria-label="Client portrait"></div><h4>John Deo</h4><p>Lorem ipsum dolor sit amet, conse ctetur adipiscing elit, sed do eius mod tempor incididunt ut labore et dolore magna aliqua.</p><div class="stars">★★★★★</div></div>
<div class="card" style="left:478px"><div class="avatar" role="img" aria-label="Client portrait"></div><h4>John Deo</h4><p>Lorem ipsum dolor sit amet, conse ctetur adipiscing elit, sed do eius mod tempor incididunt ut labore et dolore magna aliqua.</p><div class="stars">★★★★★</div></div>
<div class="card" style="left:740px"><div class="avatar" role="img" aria-label="Client portrait"></div><h4>John Deo</h4><p>Lorem ipsum dolor sit amet, conse ctetur adipiscing elit, sed do eius mod tempor incididunt ut labore et dolore magna aliqua.</p><div class="stars">★★★★★</div></div>
<div class="card faded" style="left:1002px"><div class="avatar" role="img" aria-label="Client portrait"></div><h4>John Deo</h4><p>Lorem ipsum dolor sit amet, conse ctetur adipiscing elit, sed do eius mod tempor incididunt ut labore et dolore magna aliqua.</p><div class="stars">★★★★★</div></div>
<div class="dots"><span></span><span class="on"></span><span></span><span></span></div>

<!-- contact -->
<section class="contact">
  <div role="img" aria-label="Photo of a smiling support representative in a dark blazer" class="abs" style="left:585px;top:0;width:545px;height:750px;background:linear-gradient(180deg,#e6e7eb 0%,#c9cbd1 40%,#1c1d22 75%,#0c0c0f 100%)"></div>
</section>
<div class="title" style="left:110px;top:2626px"><b>GET IN</b> TOUCH</div>
<div class="rule" style="left:110px;top:2676px"></div>
<div class="field" style="top:2711px">Full Name</div>
<div class="field" style="top:2769px">Email Address</div>
<div class="field" style="top:2827px">Phone number</div>
<div class="field" style="top:2885px">Address</div>
<div class="field" style="top:2943px;height:135px">Message</div>
<div class="btn" style="left:110px;top:3100px;width:191px;height:47px">SUBMIT</div>

<!-- footer -->
<svg class="abs" style="left:0;top:3214px" width="1200" height="430">
  <polygon points="0,84 600,4 1200,84 1200,430 0,430" fill="var(--black)"/>
  <polyline points="0,85 600,5" fill="none" stroke="var(--blue)" stroke-width="5"/>
  <line x1="96" y1="350" x2="1158" y2="350" stroke="#6b6b6b" stroke-width="1"/>
  <rect x="0" y="424" width="1200" height="6" fill="var(--blue)"/>
</svg>
<div class="brand" style="left:119px;top:3372px;font-size:36px;font-weight:500"><span class="dot"></span>NimbaVault</div>
<p class="abs foot-text" style="left:119px;top:3459px;width:260px">Lorem ipsum dolor sit amet, consectetur adipiscing elit, sed do eiusmod tempor incididunt ut labore et aliqua.</p>

<div class="foot-h" style="left:408px">QIUCK LINKS</div>
<ul class="foot-list" style="left:408px"><li>Home</li><li>About us</li><li>Services</li><li>Testimonials</li><li>Contact Us</li></ul>
<div class="foot-h" style="left:631px">IMPORTANT</div>
<ul class="foot-list" style="left:631px"><li>Privacy Policy</li><li>Refund Policy</li><li>Terms &amp; Conditions</li><li>Sitmap</li></ul>
<div class="foot-h" style="left:845px">CONTACT INFO</div>
<svg class="abs" style="left:847px;top:3395px" width="14" height="18"><path d="M7,1 a6,6 0 0 1 6,6 c0,4 -6,10 -6,10 c0,0 -6,-6 -6,-10 a6,6 0 0 1 6,-6z" fill="#fff"/><circle cx="7" cy="7" r="2.2" fill="#000"/></svg>
<p class="abs foot-text" style="left:880px;top:3390px;width:260px;line-height:30px;font-size:14px">123 Lorem ipsum dolor sit amet, consectetur adipiscing</p>
<svg class="abs" style="left:846px;top:3462px" width="16" height="16"><path d="M3,1 l3,0 l1.5,4 l-2,1.5 a9,9 0 0 0 4.5,4.5 l1.5,-2 l4,1.5 l0,3 a2,2 0 0 1 -2,2 a14,14 0 0 1 -12.5,-12.5 a2,2 0 0 1 2,-2z" fill="#fff"/></svg>
<p class="abs foot-text" style="left:880px;top:3458px;font-size:14px">+ 123 456 7890</p>
<svg class="abs" style="left:846px;top:3507px" width="17" height="13"><rect x=".5" y=".5" width="16" height="12" rx="1" fill="#fff"/><polyline points="1,1 8.5,7 16,1" fill="none" stroke="#000" stroke-width="1.3"/></svg>
<p class="abs foot-text" style="left:880px;top:3501px;font-size:14px">info@nimbavault.example</p>

<div class="social"><span></span><span></span><span></span><span></span></div>
<p class="abs foot-text" style="left:0;width:1200px;text-align:center;top:3580px;font-size:12px">© Copyrights 2021 <b>NIMBAVAULT</b> &nbsp;| &nbsp; All Rights Reserved</p>
</body>
</html>
```